Quillbay.vc needs a better website design!

We need a new and better website for Quillbay.vc. We're a Canadian venture capital firm that invests in innovative entrepreneurs. We compete against the following websites: tormelo.vc, brightvalefund.ca, kestrowvc.com, and dovaran.vc. We're a diverse group of partners and we're dedicated to the founders we invest in.
Updates

I don’t really like stock photos of random people as part of the website design…so please try to stay away from using those images. Thanks, Owen

Target Market(s)

Canadian entrepreneurs and investors

Industry/Entity Type

Venture capital, finance, investment, entrepreneurship

Coding

Coded - Design and coding required

Number of Pages Required

4 page

Font styles to use
Sans Serif

Colors

Designer to choose colors to be used in the design.

Requirements
Must have
• Clean crisp overall design. Fast and to the point.
Nice to have
• Check out www.quillbay.vc - I did it myself and it is too basic and too wordy.
Should not have
• No stock images with random people in them! Not too wordy or with too many large images that are slow to load.

```html
<!DOCTYPE html>
<html lang="en">
<head>
<meta charset="utf-8">
<title>Quillbay.vc — Homepage concepts</title>
<link rel="stylesheet" href="https://fonts.googleapis.com/css2?family=Montserrat:wght@400;500;600;700&display=swap">
<style>
:root{
  --board:#f1f1f1;
  --green:#7a9a2e;
  --lime:#b8d13a;
  --ink:#1f1f1f;
  --text:#3a3a3a;
  --muted:#5a5a5a;
  --soft:#f5f5f5;
  --line:#e2e2e2;
  --footer:#222222;
  --white:#ffffff;
}
*{box-sizing:border-box;margin:0;padding:0}
html,body{width:947px;height:1200px;overflow:hidden}
body{background:var(--board);font-family:"Montserrat",Arial,sans-serif;color:var(--text);position:relative}

.page{position:absolute;top:57px;width:606px;transform:scale(0.5545);transform-origin:0 0;background:var(--white);box-shadow:0 6px 30px rgba(0,0,0,.12);overflow:hidden}
.page--peaks{left:95px}
.page--desk{left:516px}
.page section,.page header,.page footer{position:relative;width:606px}

/* header */
.site-header{height:70px;background:var(--white)}
.brand{position:absolute;left:56px;display:flex;flex-direction:column;align-items:center;gap:4px}
.brand-dot{width:40px;height:40px;border-radius:50%;background:var(--green)}
.brand-name{font-size:11px;font-weight:700;color:var(--green);letter-spacing:.5px}
.site-header .brand{top:7px}
.contact-top{position:absolute;right:56px;top:14px;font-size:8.5px;font-weight:500;color:var(--ink);display:flex;align-items:center;gap:3px}
.contact-top a{color:var(--green);text-decoration:none;font-weight:400}
.mail{width:9px;height:7px;background:var(--green);border-radius:1px;display:inline-block}
.nav{position:absolute;right:56px;top:43px;display:flex;gap:15px;font-size:8.5px;font-weight:500;color:var(--ink)}
.nav .active{color:var(--green)}

/* heroes */
.hero{overflow:hidden}
.hero--peaks{height:337px;background:linear-gradient(180deg,#5d79a0 0%,#7a8fa8 35%,#51657f 62%,#2d3b2a 85%,#1f2a1b 100%)}
.hero--desk{height:368px;background:linear-gradient(120deg,#4e473c 0%,#7c705f 35%,#a5a3a0 60%,#6e6253 100%)}
.hero--desk::after{content:"";position:absolute;inset:0;background:rgba(20,18,14,.35)}
.hero-layer{position:absolute;inset:0;z-index:1}
.hero-title{position:absolute;color:var(--white);font-weight:700}
.hero--peaks .hero-title{top:75px;left:0;right:0;text-align:center;font-size:44px;letter-spacing:14px}
.hero--desk .hero-title{top:112px;left:56px;font-size:40px}
.hero-sub{position:absolute;color:var(--white);font-weight:500}
.hero--peaks .hero-sub{top:133px;left:105px;width:396px;text-align:center;font-size:12.5px;line-height:19px}
.hero--desk .hero-sub{top:165px;left:56px;width:320px;font-size:10.5px;line-height:17px}
.btn{position:absolute;background:var(--green);color:var(--white);font-size:9px;font-weight:600;display:flex;align-items:center;justify-content:center;letter-spacing:.2px}
.hero--peaks .btn{left:249px;top:205px;width:108px;height:33px}
.hero--desk .btn{left:57px;top:232px;width:108px;height:32px}
.site-header--overlay{position:absolute;top:0;left:0;height:90px;background:transparent;z-index:2}
.site-header--overlay .brand{top:12px}
.site-header--overlay .contact-top,.site-header--overlay .nav{color:var(--white)}
.site-header--overlay .nav{top:38px}

/* shared section type */
.eyebrow{position:absolute;font-size:10.5px;font-weight:600;color:var(--green);letter-spacing:.2px}
.heading{position:absolute;font-size:18.5px;font-weight:500;line-height:23px;color:var(--ink)}
.center{left:0;right:0;text-align:center}

/* who we are */
.who{height:303px}
.who .eyebrow{left:56px;top:33px}
.who .heading{left:56px;top:55px;width:290px}
.perk{position:absolute;left:56px;display:flex;gap:8px;align-items:flex-start}
.perk-icon{width:58px;height:58px;border-radius:50%;background:#eeeeee;display:flex;align-items:center;justify-content:center;flex:none}
.perk p{font-size:8.5px;line-height:14px;color:var(--text);width:175px;padding-top:6px}
.perk--mentor{top:141px}
.perk--intro{top:205px}
.who-photo{position:absolute;left:342px;top:42px;width:220px;height:220px;border-radius:50%;border:4px solid var(--green);background:radial-gradient(circle at 45% 40%,#e9e6df 0%,#c9b9a0 45%,#9a7550 100%)}

/* what we fund */
.fund{height:285px;background:var(--soft)}
.fund .eyebrow{top:37px}
.fund .heading{top:58px}
.feature{position:absolute;top:118px;width:160px;text-align:center}
.feature svg{display:block;margin:0 auto 10px}
.feature-label{font-size:8.5px;font-weight:500;color:var(--green);margin-bottom:6px}
.feature-text{font-size:10.5px;line-height:16px;color:var(--ink)}

/* what we look for */
.lookfor{height:339px}
.look-frame{position:absolute;left:49px;top:44px;width:203px;height:256px;border-left:1px solid var(--green);border-bottom:1px solid var(--green)}
.look-photo{position:absolute;left:56px;top:39px;width:203px;height:256px;background:linear-gradient(160deg,#1f3350 0%,#4b6585 30%,#dfe3e8 55%,#c8ced6 75%,#5a6d88 100%)}
.lookfor .eyebrow{left:289px;top:39px}
.lookfor .heading{left:289px;top:60px;width:280px}
.checks{position:absolute;left:289px;top:143px;display:grid;grid-template-columns:147px 140px;row-gap:8px;list-style:none}
.checks li{font-size:8px;color:var(--text);display:flex;align-items:center;gap:5px;height:13px}
.checks li::before{content:"✓";width:8px;height:8px;border-radius:50%;background:var(--green);color:var(--white);font-size:6px;line-height:8px;text-align:center;font-weight:700}
.lookfor .btn{left:289px;top:263px;width:81px;height:30px;font-size:8.5px}

/* get in touch */
.touch{height:188px;background:linear-gradient(180deg,#9ba08f 0%,#8d9488 45%,#5c6e7d 75%,#2e4258 100%)}
.touch .eyebrow{top:30px;color:var(--lime)}
.touch .heading{top:52px;color:var(--white)}
.touch .btn{left:262px;top:115px;width:81px;height:30px;font-size:8.5px}

/* featured companies */
.featured{height:253px}
.featured .eyebrow{top:37px}
.featured .heading{top:58px}
.logo-grid{position:absolute;left:56px;top:107px;width:494px;display:grid;grid-template-columns:repeat(5,95px);gap:6px 4.75px}
.logo-cell{height:48px;border:1px solid var(--line);display:flex;align-items:center;justify-content:center;font-size:11px;font-weight:600;color:var(--ink)}

/* footer */
.site-footer{height:184px;background:var(--footer);color:var(--white)}
.site-footer .brand{top:18px;left:56px;gap:8px}
.site-footer .brand-dot{width:72px;height:72px}
.site-footer .brand-name{font-size:19px}
.foot-col{position:absolute;top:26px}
.foot-col h4{font-size:8.5px;font-weight:600;margin-bottom:12px}
.foot-col ul{list-style:none}
.foot-col li{font-size:7.5px;line-height:15.7px;color:#dddddd}
.foot-links{left:248px}
.foot-contact{left:391px}
.foot-mail{font-size:8.5px;font-weight:500;display:flex;align-items:center;gap:5px}
.socials{display:flex;gap:5px;margin-top:14px}
.socials span{width:23px;height:23px;border-radius:50%;border:1px solid var(--white)}
.foot-rule{position:absolute;left:56px;right:56px;top:137px;border-top:1px solid #3c3c3c}
.copyright{position:absolute;left:0;right:0;top:152px;text-align:center;font-size:7.5px;color:#dddddd}
.page--desk .site-footer{height:182px}
</style>
</head>
<body>

<!-- Concept A: mountain hero -->
<div class="page page--peaks">
  <header class="site-header">
    <div class="brand"><span class="brand-dot"></span><span class="brand-name">QUILLBAY.VC</span></div>
    <div class="contact-top"><span class="mail"></span>Contact Us: <a>owen@quillbay.vc</a></div>
    <nav class="nav"><span class="active">HOME</span><span>TEAM</span><span>COMPANIES</span><span>WHAT WE LOOK FOR</span></nav>
  </header>

  <section class="hero hero--peaks" role="img" aria-label="Photograph of snow-capped mountain peaks above a pine forest">
    <div class="hero-layer">
      <h1 class="hero-title">QUILLBAY</h1>
      <p class="hero-sub">Venture capital firm that invests in innovative seed-stage technology companies in Western Canada focused on B2B and SaaS markets.</p>
      <span class="btn">GET MORE INFO</span>
    </div>
  </section>

  <section class="who">
    <p class="eyebrow">WHO WE ARE</p>
    <h2 class="heading">We are serial entrepreneurs and venture capital investors who provide:</h2>
    <div class="perk perk--mentor">
      <span class="perk-icon"><svg width="30" height="30" viewBox="0 0 30 30" fill="none" stroke="#7a9a2e" stroke-width="1.6"><circle cx="9" cy="8" r="4"/><path d="M13 8h8a4 4 0 0 1 0 8H9a4 4 0 0 0 0 8h14"/><path d="M20 21l3 3-3 3"/></svg></span>
      <p>Mentoring and strategic advice to help you grow your company quickly and efficiently</p>
    </div>
    <div class="perk perk--intro">
      <span class="perk-icon"><svg width="30" height="30" viewBox="0 0 30 30" fill="#7a9a2e"><circle cx="9" cy="9" r="4"/><path d="M2 26c0-6 3-10 7-10s7 4 7 10z"/><rect x="18" y="20" width="2" height="6"/><rect x="21.5" y="17" width="2" height="9"/><rect x="25" y="14" width="2" height="12"/><text x="20" y="11" font-size="10" font-family="Montserrat,sans-serif" font-weight="700">$</text></svg></span>
      <p>Investor introductions to help you raise additional follow-on funding for your startup</p>
    </div>
    <div class="who-photo" role="img" aria-label="Photograph of a desk with a laptop, notebook and printed charts"></div>
  </section>

  <section class="fund">
    <p class="eyebrow center">WHAT WE FUND</p>
    <h2 class="heading center">Canada's leading nationwide<br>seed stage venture fund</h2>
    <div class="feature" style="left:52px">
      <svg width="56" height="52" viewBox="0 0 56 52" fill="none" stroke="#555" stroke-width="1.5"><rect x="10" y="20" width="36" height="24"/><path d="M4 44h48v4H4z"/><path d="M28 6c5 5 5 14 3 20h-6c-2-6-2-15 3-20z" stroke="#7a9a2e"/><circle cx="28" cy="16" r="2" stroke="#7a9a2e"/></svg>
      <p class="feature-label">Venture Capital Funding</p>
      <p class="feature-text">At early-stage &amp;<br>seed stage</p>
    </div>
    <div class="feature" style="left:223px">
      <svg width="56" height="52" viewBox="0 0 56 52" fill="none" stroke="#555" stroke-width="1.5"><circle cx="14" cy="9" r="5"/><path d="M6 34V22a8 8 0 0 1 16 0v12"/><circle cx="42" cy="23" r="5"/><path d="M34 48V36a8 8 0 0 1 16 0v12"/><path d="M26 6h10l-3-3M30 44H20l3 3" stroke="#7a9a2e"/></svg>
      <p class="feature-label">$250K TO $700K</p>
      <p class="feature-text">Various B2B and<br>SaaS sectors</p>
    </div>
    <div class="feature" style="left:403px">
      <svg width="56" height="52" viewBox="0 0 56 52" fill="none" stroke="#555" stroke-width="1.5" stroke-dasharray="2 2"><circle cx="28" cy="26" r="6" stroke="#7a9a2e" stroke-dasharray="none"/><circle cx="28" cy="26" r="2.5" fill="#7a9a2e" stroke="none"/><path d="M28 2v14M28 36v14M4 26h14M38 26h14M10 10l10 10M46 10L36 20M10 42l10-10M46 42L36 32"/></svg>
      <p class="feature-label">Sector Agnostic</p>
      <p class="feature-text">Diversified and<br>Innovative portfolio</p>
    </div>
  </section>

  <section class="lookfor">
    <div class="look-frame"></div>
    <div class="look-photo" role="img" aria-label="Photograph of a tablet and printed financial charts on a table"></div>
    <p class="eyebrow">WHAT WE LOOK FOR</p>
    <h2 class="heading">We invest in innovative technology companies with these characteristics</h2>
    <ul class="checks">
      <li>Founding Team</li><li>Customers</li>
      <li>Total Addressable Market</li><li>Business Model</li>
      <li>Product Market Fit</li><li>Competitive Advantage</li>
      <li>Timing</li><li>Funding</li>
      <li>Problem</li><li>Deal Terms</li>
    </ul>
    <span class="btn">READ MORE</span>
  </section>

  <section class="touch" role="img" aria-label="Photograph looking up at glass office towers">
    <p class="eyebrow center">GET IN TOUCH</p>
    <h2 class="heading center">Contact us today if you have<br>what we're looking for</h2>
    <span class="btn">CONTACT US</span>
  </section>

  <section class="featured">
    <p class="eyebrow center">FEATURED COMPANIES</p>
    <h2 class="heading center">Our innovative portfolio companies!</h2>
    <div class="logo-grid">
      <span class="logo-cell">Tidemarrow</span><span class="logo-cell">Lumaroute</span><span class="logo-cell">Brisketa</span><span class="logo-cell">Corvane</span><span class="logo-cell">Halvero</span>
      <span class="logo-cell">Jorvessa</span><span class="logo-cell">Plainwell</span><span class="logo-cell">Gatenook</span><span class="logo-cell">Pellwick</span><span class="logo-cell">Vorrix</span>
    </div>
  </section>

  <footer class="site-footer">
    <div class="brand"><span class="brand-dot"></span><span class="brand-name">QUILLBAY.VC</span></div>
    <div class="foot-col foot-links"><h4>Quick Links</h4><ul><li>Home</li><li>Team</li><li>Companies</li><li>What We Look For</li></ul></div>
    <div class="foot-col foot-contact"><h4>Contact Us</h4><p class="foot-mail"><span class="mail"></span>owen@quillbay.vc</p><div class="socials"><span></span><span></span><span></span></div></div>
    <div class="foot-rule"></div>
    <p class="copyright">Copyright © 2021, Quillbay. All rights reserved.</p>
  </footer>
</div>

<!-- Concept B: desk hero -->
<div class="page page--desk">
  <section class="hero hero--desk" role="img" aria-label="Photograph of hands reviewing printed charts with a pen">
    <header class="site-header site-header--overlay">
      <div class="brand"><span class="brand-dot"></span><span class="brand-name">QUILLBAY.VC</span></div>
      <div class="contact-top"><span class="mail"></span>Contact Us: <a>owen@quillbay.vc</a></div>
      <nav class="nav"><span class="active">HOME</span><span>TEAM</span><span>COMPANIES</span><span>WHAT WE LOOK FOR</span></nav>
    </header>
    <div class="hero-layer">
      <h1 class="hero-title">QUILLBAY</h1>
      <p class="hero-sub">Venture capital firm that invests in innovative seed-stage technology companies in Western Canada focused on B2B and SaaS markets.</p>
      <span class="btn">GET MORE INFO</span>
    </div>
  </section>

  <section class="who">
    <p class="eyebrow">WHO WE ARE</p>
    <h2 class="heading">We are serial entrepreneurs and venture capital investors who provide:</h2>
    <div class="perk perk--mentor">
      <span class="perk-icon"><svg width="30" height="30" viewBox="0 0 30 30" fill="none" stroke="#7a9a2e" stroke-width="1.6"><circle cx="9" cy="8" r="4"/><path d="M13 8h8a4 4 0 0 1 0 8H9a4 4 0 0 0 0 8h14"/><path d="M20 21l3 3-3 3"/></svg></span>
      <p>Mentoring and strategic advice to help you grow your company quickly and efficiently</p>
    </div>
    <div class="perk perk--intro">
      <span class="perk-icon"><svg width="30" height="30" viewBox="0 0 30 30" fill="#7a9a2e"><circle cx="9" cy="9" r="4"/><path d="M2 26c0-6 3-10 7-10s7 4 7 10z"/><rect x="18" y="20" width="2" height="6"/><rect x="21.5" y="17" width="2" height="9"/><rect x="25" y="14" width="2" height="12"/><text x="20" y="11" font-size="10" font-family="Montserrat,sans-serif" font-weight="700">$</text></svg></span>
      <p>Investor introductions to help you raise additional follow-on funding for your startup</p>
    </div>
    <div class="who-photo" role="img" aria-label="Photograph of a desk with a laptop, notebook and printed charts"></div>
  </section>

  <section class="fund">
    <p class="eyebrow center">WHAT WE FUND</p>
    <h2 class="heading center">Canada's leading nationwide<br>seed stage venture fund</h2>
    <div class="feature" style="left:52px">
      <svg width="56" height="52" viewBox="0 0 56 52" fill="none" stroke="#555" stroke-width="1.5"><rect x="10" y="20" width="36" height="24"/><path d="M4 44h48v4H4z"/><path d="M28 6c5 5 5 14 3 20h-6c-2-6-2-15 3-20z" stroke="#7a9a2e"/><circle cx="28" cy="16" r="2" stroke="#7a9a2e"/></svg>
      <p class="feature-label">Venture Capital Funding</p>
      <p class="feature-text">At early-stage &amp;<br>seed stage</p>
    </div>
    <div class="feature" style="left:223px">
      <svg width="56" height="52" viewBox="0 0 56 52" fill="none" stroke="#555" stroke-width="1.5"><circle cx="14" cy="9" r="5"/><path d="M6 34V22a8 8 0 0 1 16 0v12"/><circle cx="42" cy="23" r="5"/><path d="M34 48V36a8 8 0 0 1 16 0v12"/><path d="M26 6h10l-3-3M30 44H20l3 3" stroke="#7a9a2e"/></svg>
      <p class="feature-label">$250K TO $700K</p>
      <p class="feature-text">Various B2B and<br>SaaS sectors</p>
    </div>
    <div class="feature" style="left:403px">
      <svg width="56" height="52" viewBox="0 0 56 52" fill="none" stroke="#555" stroke-width="1.5" stroke-dasharray="2 2"><circle cx="28" cy="26" r="6" stroke="#7a9a2e" stroke-dasharray="none"/><circle cx="28" cy="26" r="2.5" fill="#7a9a2e" stroke="none"/><path d="M28 2v14M28 36v14M4 26h14M38 26h14M10 10l10 10M46 10L36 20M10 42l10-10M46 42L36 32"/></svg>
      <p class="feature-label">Sector Agnostic</p>
      <p class="feature-text">Diversified and<br>Innovative portfolio</p>
    </div>
  </section>

  <section class="lookfor">
    <div class="look-frame"></div>
    <div class="look-photo" role="img" aria-label="Photograph of a tablet and printed financial charts on a table"></div>
    <p class="eyebrow">WHAT WE LOOK FOR</p>
    <h2 class="heading">We invest in innovative technology companies with these characteristics</h2>
    <ul class="checks">
      <li>Founding Team</li><li>Customers</li>
      <li>Total Addressable Market</li><li>Business Model</li>
      <li>Product Market Fit</li><li>Competitive Advantage</li>
      <li>Timing</li><li>Funding</li>
      <li>Problem</li><li>Deal Terms</li>
    </ul>
    <span class="btn">READ MORE</span>
  </section>

  <section class="touch" role="img" aria-label="Photograph looking up at glass office towers">
    <p class="eyebrow center">GET IN TOUCH</p>
    <h2 class="heading center">Contact us today if you have<br>what we're looking for</h2>
    <span class="btn">CONTACT US</span>
  </section>

  <section class="featured">
    <p class="eyebrow center">FEATURED COMPANIES</p>
    <h2 class="heading center">Our innovative portfolio companies!</h2>
    <div class="logo-grid">
      <span class="logo-cell">Tidemarrow</span><span class="logo-cell">Lumaroute</span><span class="logo-cell">Brisketa</span><span class="logo-cell">Corvane</span><span class="logo-cell">Halvero</span>
      <span class="logo-cell">Jorvessa</span><span class="logo-cell">Plainwell</span><span class="logo-cell">Gatenook</span><span class="logo-cell">Pellwick</span><span class="logo-cell">Vorrix</span>
    </div>
  </section>

  <footer class="site-footer">
    <div class="brand"><span class="brand-dot"></span><span class="brand-name">QUILLBAY.VC</span></div>
    <div class="foot-col foot-links"><h4>Quick Links</h4><ul><li>Home</li><li>Team</li><li>Companies</li><li>What We Look For</li></ul></div>
    <div class="foot-col foot-contact"><h4>Contact Us</h4><p class="foot-mail"><span class="mail"></span>owen@quillbay.vc</p><div class="socials"><span></span><span></span><span></span></div></div>
    <div class="foot-rule"></div>
    <p class="copyright">Copyright © 2021, Quillbay. All rights reserved.</p>
  </footer>
</div>

</body>
</html>
```